Fun, Colorful, Classy ,& Stylish Wine Bacholorette Labels

Thanks For Stopping By, My Hope is That we Can Knock this out of The Park :)
Ok, So Here is Our Big Idea.

We are going to be launching another product on zelvora that are similar to these below.
https://www.zelvora.com/Bottle-Labels-Engagement-Party-Bachelorette/dp/Q73KXM82WD/ref=sr_1_8?s=home-garden&ie=UTF8&qid=4817206359&sr=1-8&keywords=bridal+wine+labels&dpID=83tu2KMPqZR&preST=SY300_QL70&dpSrc=srch
https://www.zelvora.com/Wow-Look-Whos-Tying-Knot/dp/Q52WLP47ZN/ref=pd_sim_79_3?_encoding=UTF8&pd_rd_i=Q52WLP47ZN&pd_rd_r=KWMPX38D71JZ46Q20V93&pd_rd_w=tqX4p&pd_rd_wg=f9LzR&psc=1&refRID=KWMPX38D71JZ46Q20V93
https://www.zelvora.com/Bachelorette-Wedding-Wine-Bottle-Labels/dp/Q96HRT3VX8/ref=pd_sim_79_2?_encoding=UTF8&pd_rd_i=Q96HRT3VX8&pd_rd_r=KWMPX38D71JZ46Q20V93&pd_rd_w=tqX4p&pd_rd_wg=f9LzR&psc=1&refRID=KWMPX38D71JZ46Q20V93

We are going to do a few Styles.
1 Bachelorette , Engagement Party - Bridal Gift - Funny - 6Pc

We are planning to do a few more but let’s start with this one first.

size: 4'' x 5'' - mock up should also be done on the bottle. pick from one of the quotes below and design a label that will knock our socks off. :)

the wine bottle pics are just an example of another company that have done something similar.

T

Industry/Entity Type

Wedding

Font styles to use
Script

Colors
e667a6
ffffff
33a6d7
b768aa
e34197
fbee3d
abd036
33b8a4
6b449b

Requirements
Must have
• Colorful Humor and tasteful
Nice to have
• a creative spin on concept
Should not have
• should not be plain jane/ boring.

```html
<!DOCTYPE html>
<html lang="en">
<head>
<meta charset="UTF-8">
<title>Cheers to the Future Mrs. – Wine Label</title>
<link rel="stylesheet" href="https://fonts.googleapis.com/css2?family=Great+Vibes&family=Raleway:wght@300&display=swap">
<style>
  :root {
    --backdrop: #d3d3d3;
    --paper: #ffffff;
    --purple: #5b138b;
    --gold-light: #e6b86a;
    --gold: #c99552;
    --gold-deep: #a8733a;
    --ornament-soft: #f3e4c6;
  }
  html, body {
    margin: 0;
    width: 1200px;
    height: 923px;
    overflow: hidden;
    background: var(--backdrop);
  }
  .label {
    position: absolute;
    left: 298px;
    top: 84px;
    width: 603px;
    height: 754px;
    background: var(--paper);
    overflow: hidden;
  }
  .stripe {
    position: absolute;
    left: 0;
    width: 100%;
    height: 30px;
    background: var(--purple);
  }
  .ornament {
    position: absolute;
    background: radial-gradient(ellipse at center, var(--ornament-soft) 0%, rgba(243,228,198,0.35) 70%, rgba(255,255,255,0) 100%);
  }
  .frame {
    position: absolute;
    left: 48px;
    top: 112px;
    width: 496px;
    height: 516px;
    border: 6px solid var(--gold);
    border-color: var(--gold-light) var(--gold) var(--gold-deep) var(--gold);
    background: var(--paper);
  }
  .rule { position: absolute; background: var(--gold-light); }
  .rule-top { left: 48px; top: 19px; width: 340px; height: 2px; }
  .rule-bottom { left: 110px; top: 499px; width: 340px; height: 2px; }
  .rule-left { left: 18px; top: 40px; width: 1.5px; height: 460px; }
  .rule-right { left: 473px; top: 100px; width: 1.5px; height: 360px; }
  .corner-dot {
    position: absolute;
    width: 6px; height: 6px;
    background: var(--gold-deep);
    transform: rotate(45deg);
  }
  .gold-text {
    background: linear-gradient(180deg, var(--gold-light) 0%, var(--gold) 55%, var(--gold-deep) 100%);
    -webkit-background-clip: text;
    background-clip: text;
    color: transparent;
    line-height: 1.6;
    padding: 0 24px;
  }
  .cheers, .future, .mrs {
    position: absolute;
    font-family: "Great Vibes", cursive;
    white-space: nowrap;
  }
  .cheers { left: 22px; top: 18px; font-size: 160px; }
  .to-the {
    position: absolute;
    left: 178px;
    top: 186px;
    font-family: "Raleway", sans-serif;
    font-weight: 300;
    font-size: 28px;
    line-height: 1;
    letter-spacing: 8px;
    color: var(--gold);
  }
  .future { left: 138px; top: 194px; font-size: 84px; }
  .mrs { left: 40px; top: 317px; font-size: 175px; line-height: 1; color: var(--purple); }
  .rings {
    position: absolute;
    left: 362px;
    top: 204px;
    width: 96px;
    height: 120px;
    background: radial-gradient(circle, var(--ornament-soft) 0%, rgba(243,228,198,0.2) 75%, rgba(255,255,255,0) 100%);
  }
</style>
</head>
<body>
  <div class="label">
    <div class="stripe" style="top:122px"></div>
    <div class="stripe" style="top:202px"></div>
    <div class="stripe" style="top:282px"></div>
    <div class="stripe" style="top:362px"></div>
    <div class="stripe" style="top:442px"></div>
    <div class="stripe" style="top:522px"></div>
    <div class="stripe" style="top:602px"></div>

    <div class="ornament" role="img" aria-label="Gold filigree corner ornament" style="left:0;top:0;width:115px;height:100px"></div>
    <div class="ornament" role="img" aria-label="Gold filigree crest ornament" style="left:225px;top:0;width:155px;height:75px"></div>
    <div class="ornament" role="img" aria-label="Gold filigree corner ornament" style="right:0;top:0;width:115px;height:100px"></div>
    <div class="ornament" role="img" aria-label="Gold filigree corner ornament" style="left:0;bottom:0;width:115px;height:100px"></div>
    <div class="ornament" role="img" aria-label="Gold filigree crest ornament" style="left:225px;bottom:0;width:155px;height:75px"></div>
    <div class="ornament" role="img" aria-label="Gold filigree corner ornament" style="right:0;bottom:0;width:115px;height:100px"></div>

    <div class="frame">
      <div class="rule rule-top"></div>
      <div class="rule rule-bottom"></div>
      <div class="rule rule-left"></div>
      <div class="rule rule-right"></div>
      <div class="corner-dot" style="left:22px;top:22px"></div>
      <div class="corner-dot" style="left:466px;top:486px"></div>

      <div class="cheers gold-text">Cheers</div>
      <div class="to-the">TO THE</div>
      <div class="future gold-text">Future</div>
      <div class="rings" role="img" aria-label="Gold line drawing of two wedding rings with a diamond"></div>
      <div class="mrs">Mrs.</div>
    </div>
  </div>
</body>
</html>
```